Dov's Personal Training -> also needs a logo

Services Frankston, Mornington, and Somerville

Specializes in in-home personal training

VaultPace style workouts

Not really preferential colors but needs to look modern and not stock photo

Industry/Entity Type

Training

Requirements
Must have
• 30% off first time customers on a package of 10

```html
<!DOCTYPE html>
<html lang="en">
<head>
<meta charset="utf-8">
<title>Dov's Personal Training</title>
<link rel="stylesheet" href="https://fonts.googleapis.com/css2?family=Arimo:wght@700&family=Jost:wght@400;500;700&display=swap">
<style>
  :root {
    --bg-top: #ffffff;
    --bg-bottom: #d6d8f6;
    --brand-blue: #2f3cf0;
    --label-blue: #1f72b6;
    --offer-frame: #aaa3f5;
    --offer-fill: #40c3ec;
    --wave-cyan: #41c4ee;
    --wave-navy: #1c6bb6;
    --wave-green: #66ee88;
    --wave-mint: #4cf6d0;
    --white: #ffffff;
  }
  * { margin: 0; padding: 0; box-sizing: border-box; }
  html, body { width: 1200px; height: 900px; overflow: hidden; }
  .canvas {
    position: relative;
    width: 1200px;
    height: 900px;
    overflow: hidden;
    background: linear-gradient(180deg, var(--bg-top) 0%, var(--bg-bottom) 85%);
    font-family: "Jost", "Century Gothic", sans-serif;
    color: var(--brand-blue);
  }
  .brand {
    position: absolute;
    left: 600px;
    top: 110px;
    width: 560px;
    text-align: center;
    font-weight: 500;
    color: var(--brand-blue);
    line-height: 1;
  }
  .brand-name { font-size: 82px; letter-spacing: 2px; }
  .brand-tag { font-size: 54px; margin-top: 14px; letter-spacing: 1px; }
  .info {
    position: absolute;
    left: 67px;
    font-size: 32px;
    line-height: 36px;
    text-transform: uppercase;
    letter-spacing: 0.5px;
  }
  .info-services { top: 410px; }
  .info-specialties { top: 492px; }
  .label { font-weight: 700; color: var(--label-blue); letter-spacing: -0.5px; }
  .offer {
    position: absolute;
    left: 743px;
    top: 503px;
    width: 396px;
    height: 183px;
    padding: 15px 16px;
    background: var(--offer-frame);
    border-radius: 42px;
  }
  .offer-inner {
    height: 100%;
    background: var(--offer-fill);
    border-radius: 30px;
    padding: 6px 0 0 14px;
    font-family: "Arimo", Arial, sans-serif;
    font-weight: 700;
    color: var(--white);
  }
  .offer-value { font-size: 74px; line-height: 74px; letter-spacing: -1px; }
  .offer-terms { font-size: 30px; line-height: 32px; letter-spacing: -0.5px; }
  .waves { position: absolute; left: 0; top: 0; }
</style>
</head>
<body>
<div class="canvas">
  <svg class="waves" width="1200" height="900" viewBox="0 0 1200 900" aria-hidden="true">
    <path fill="var(--wave-green)" opacity="0.8" d="M650 690 C820 700 1000 700 1200 660 L1200 900 L650 900 Z"/>
    <path fill="var(--wave-cyan)" d="M0 707 L40 707 C200 645 320 625 430 630 C600 640 760 690 900 705 C1050 720 1150 790 1200 840 L1200 900 L0 900 Z"/>
    <path fill="var(--wave-navy)" d="M0 770 C200 705 420 690 620 712 C820 735 1020 790 1200 880 L1200 900 L0 900 Z"/>
    <path fill="var(--wave-green)" d="M0 815 C160 735 360 725 560 752 C760 780 950 770 1200 720 L1200 900 L0 900 Z"/>
    <path fill="var(--wave-mint)" d="M0 900 L0 845 C150 778 350 768 560 795 C760 822 960 770 1200 705 L1200 900 Z"/>
  </svg>

  <div class="brand">
    <div class="brand-name">Dov's</div>
    <div class="brand-tag">Personal Training</div>
  </div>

  <p class="info info-services"><span class="label">Services:</span> Frankston - Mornington, and Somerville</p>

  <div class="info info-specialties">
    <p class="label">Specializes in:</p>
    <p>In-home personal training</p>
    <p>VaultPace style workouts</p>
  </div>

  <div class="offer">
    <div class="offer-inner">
      <p class="offer-value">30%OFF</p>
      <p class="offer-terms">first time customers<br>on a package of 10</p>
    </div>
  </div>
</div>
</body>
</html>
```